Celvara Health Group Presentation Folder, for Cancer Awareness, VERY COLORFUL AND MODERN

Presentation Folder I know pretty much what i want so it should be very eazy , I have included files from folders I use now rebrand them to my new company they will be fine, no sense re creating the wheel
Full Bleed Size
20.87" x 16.68"
53 x 42.4 cm
6260 x 5004 pixels
Document Trim Size
20.75" x 16.56"
52.7 x 42.1 cm
6225 x 4969 pixels

Low design quality

Industry/Entity Type

Medical

Font styles to use
Serif

Colors

Designer to choose colors to be used in the design.

Requirements
Must have
• really I am not looking for some one to redesign, we like our folder front page and would like to see new word information added., there are two folder front pages to choose from
• So Keep the original front page and redesign the back page and the pockets
• Can Make your Design off of one of the ones I already uploaded
Nice to have
• Keep the same color schemes, Keep the original front page and redesign the back page and the pockets
Should not have
• DO not recreate the front covers, use what I gave you and just rebrand

```html
<!DOCTYPE html>
<html lang="en">
<head>
<meta charset="utf-8">
<title>Celvara Health Group – Presentation Folder</title>
<link href="https://fonts.googleapis.com/css2?family=Raleway:wght@400;500;600;700;800&display=swap" rel="stylesheet">
<style>
  :root{
    --backdrop:#e6e6e8;
    --paper:#ffffff;
    --pink:#ef6f8f;
    --navy:#1b2a6b;
    --blue:#1f4fa3;
    --sky:#4ab3e6;
    --text:#444a55;
    --strip:#d3d4d6;
    --slit:#c7c8cc;
  }
  *{box-sizing:border-box;margin:0;padding:0}
  html,body{width:902px;height:1200px;overflow:hidden}
  body{background:var(--backdrop);font-family:'Raleway',sans-serif;position:relative}
  .folder{position:absolute;left:26px;top:236px;width:850px;height:728px}
  .folder-shape{position:absolute;inset:0}
  .folder > div, .folder > p, .folder > h1, .folder > h2{position:absolute}

  .family-photo{left:80px;top:38px;width:260px;height:260px;border-radius:50%;
    background:radial-gradient(circle at 45% 40%,#f3dccb 0%,#d9b59d 45%,#c6d3dc 100%)}
  .intro{left:30px;top:328px;width:358px;font-size:10.6px;line-height:1.42;color:var(--text);text-align:justify}
  .intro strong{color:var(--pink);font-weight:600}
  .motto{left:20px;top:424px;width:370px;text-align:center;font-weight:700;line-height:1.38}
  .motto .lead{color:var(--pink);font-size:13.5px}
  .motto .body{color:var(--navy);font-size:13.5px}

  .cover-title{left:440px;top:48px;width:400px;text-align:center;color:var(--pink);font-size:21.5px;font-weight:800;letter-spacing:.2px}
  .cover-sub{left:440px;top:80px;width:400px;text-align:center;color:var(--blue);font-size:10.8px;font-weight:700}
  .cover-note{left:450px;top:105px;width:380px;text-align:center;color:var(--sky);font-size:9.6px;line-height:1.35;text-transform:uppercase}
  .dinner-photo{left:468px;top:212px;width:334px;height:216px;transform:rotate(-4deg);
    border:6px solid var(--paper);box-shadow:0 3px 10px rgba(0,0,0,.35);
    background:linear-gradient(160deg,#eef3f4 0%,#d8c8b4 55%,#b99a78 100%)}
  .tagline{left:456px;top:474px;display:flex;align-items:center;gap:12px;color:var(--blue);font-size:15.5px;font-weight:500}
  .tagline .dot{width:34px;height:34px;border-radius:50%;background:var(--navy)}

  .pocket-left-label{left:70px;top:540px;width:290px;text-align:center;transform:rotate(180deg)}
  .pocket-left-label .name{color:var(--pink);font-size:17px;font-weight:500;letter-spacing:.6px;text-transform:uppercase}
  .pocket-left-label .division{color:var(--navy);font-size:11.5px;margin-top:2px}
  .pocket-right-brand{left:520px;top:585px;display:flex;align-items:center;gap:12px;transform:rotate(180deg)}
  .pocket-right-brand .mark{width:62px;height:62px;border-radius:50%;background:var(--navy)}
  .pocket-right-brand .name{color:var(--navy);font-size:22px;font-weight:800;letter-spacing:.5px;text-transform:uppercase;line-height:1.05}
</style>
</head>
<body>
  <section class="folder">
    <svg class="folder-shape" width="850" height="728" viewBox="0 0 850 728">
      <rect x="0" y="0" width="850" height="728" fill="#ffffff"/>
      <rect x="0" y="528" width="33" height="200" fill="#d3d4d6"/>
      <rect x="820" y="528" width="30" height="200" fill="#d3d4d6"/>
      <path d="M419,528 C421,610 410,690 360,728 L510,728 C455,700 432,620 432,528 Z" fill="#e6e6e8"/>
      <path d="M419,528 C421,610 410,690 360,728" fill="none" stroke="#bfc0c4" stroke-width="1"/>
      <path d="M432,528 C432,620 455,700 510,728" fill="none" stroke="#bfc0c4" stroke-width="1"/>
      <g stroke="#c7c8cc" stroke-width="1.4">
        <line x1="135" y1="592" x2="158" y2="570"/>
        <line x1="268" y1="570" x2="291" y2="592"/>
        <line x1="135" y1="635" x2="158" y2="657"/>
        <line x1="268" y1="657" x2="291" y2="635"/>
      </g>
      <path d="M330,40 A138,138 0 0 1 150,300 L66,246 C90,262 120,282 150,290 A126,126 0 0 0 320,54 Z" fill="#1b2a6b"/>
    </svg>

    <div class="family-photo" role="img" aria-label="Photo of a smiling three-generation family"></div>

    <p class="intro"><strong>Hereditary cancer screening</strong> provides vital information to help people with a strong personal or family history of cancer understand their own risk of developing the disease. With this information, they can take steps to Potentially Prevent Cancer, Delay the Onset of Cancer or Catch it at an Earlier stage when outcomes and survival rates are Better.</p>

    <div class="motto">
      <p class="lead">Don't be Afraid of the Answer:</p>
      <p class="body">Knowledge is Power and Power Eradicates Fear.<br>When You are Fearless, You Will Make all the<br>Right Choices!</p>
    </div>

    <h1 class="cover-title">HEREDITARY CANCER SCREENING</h1>
    <h2 class="cover-sub">DOCTORS ARE THE GATEKEEPERS TO GENETIC TESTING.</h2>
    <p class="cover-note">We have an obligation to help patients understand genetic<br>risk and how testing can guide heath care decisions.</p>

    <div class="dinner-photo" role="img" aria-label="Photo of a family sharing a meal around an outdoor table"></div>

    <div class="tagline"><span class="dot"></span><span>The test you order FOR your patients</span></div>

    <div class="pocket-left-label">
      <p class="name">Celvara Health Group</p>
      <p class="division">a division of Brightlane Medical Sales LLC</p>
    </div>

    <div class="pocket-right-brand">
      <span class="mark"></span>
      <span class="name">Celvara<br>Health<br>Group</span>
    </div>
  </section>
</body>
</html>
```